Salon and Spa Distributor Business Card

Need a business card. We are are distributor in the salon and spa industry. We identify with natural beauty. Need a card with:
Company Name: Petal Quarry"
Title: "President & CEO"
Address
Company Phone number
email
website
Tag Line:" The Professional Salon Source"

Industry/Entity Type

Business

Contact Information for Business Card

Name: Dov Strommen
Title: "President & CEO"
Address: 31 Harlow Ln, Bexmoor, NJ 07813
Company Phone number: 800-463-5918
email: dovstrommen@petalquarry.example
website: www.petalquarry.example

Requirements
Should not have
• No black backgrounds

```html
<!DOCTYPE html>
<html lang="en">
<head>
<meta charset="utf-8">
<title>Petal Quarry — Business Card</title>
<link rel="stylesheet" href="https://fonts.googleapis.com/css2?family=Montserrat:wght@700&family=Questrial&display=swap">
<style>
  :root {
    --page: #ecebe8;
    --card: #ffffff;
    --green-deep: #1b7a2c;
    --green-mid: #2e9a3a;
    --green-bright: #5fc23f;
    --ink-green: #1e6b2a;
    --ink-dark: #2c3a2e;
    --on-green: #ffffff;
  }
  * { margin: 0; padding: 0; box-sizing: border-box; }
  html, body { width: 1200px; height: 716px; overflow: hidden; background: var(--page); }
  .card {
    position: absolute; left: 100px; top: 72px; width: 1000px; height: 572px;
    background: var(--card); overflow: hidden;
    box-shadow: 0 6px 24px rgba(0,0,0,.18);
  }
  .waves { position: absolute; inset: 0; }
  .brand { position: absolute; left: 80px; top: 84px; }
  .brand-mark { width: 64px; height: 64px; border-radius: 50%; background: var(--green-bright); margin: 0 0 14px 120px; }
  .brand-name {
    font-family: "Questrial", sans-serif; font-size: 52px; color: var(--green-mid); line-height: 1;
  }
  .brand-tagline {
    font-family: "Questrial", sans-serif; font-size: 21px; color: var(--ink-green); margin-top: 8px; padding-left: 4px;
  }
  .person { position: absolute; right: 60px; top: 150px; text-align: right; }
  .person-name { font-family: "Montserrat", sans-serif; font-weight: 700; font-size: 32px; color: var(--ink-green); }
  .person-title { font-family: "Questrial", sans-serif; font-size: 18px; color: var(--ink-dark); margin-top: 4px; }
  .contact {
    position: absolute; right: 40px; top: 420px; list-style: none;
    font-family: "Questrial", sans-serif; font-size: 21px; color: var(--on-green); text-align: right;
  }
  .contact li { display: flex; justify-content: flex-end; align-items: center; gap: 12px; height: 33px; }
  .contact svg { width: 20px; height: 20px; flex: none; }
</style>
</head>
<body>
  <div class="card">
    <svg class="waves" viewBox="0 0 1000 572" preserveAspectRatio="none" aria-hidden="true">
      <path d="M0 250 C 200 300, 420 360, 1000 372 L 1000 380 C 440 372, 210 320, 0 268 Z" fill="var(--green-bright)"/>
      <path d="M0 278 C 220 330, 440 385, 1000 392 L 1000 400 C 430 400, 210 350, 0 300 Z" fill="var(--green-mid)"/>
      <path d="M0 318 C 220 365, 460 410, 1000 408 L 1000 572 L 0 572 Z" fill="var(--green-deep)"/>
    </svg>

    <div class="brand">
      <div class="brand-mark"></div>
      <div class="brand-name">Petal Quarry</div>
      <div class="brand-tagline">The Professional Salon Source</div>
    </div>

    <div class="person">
      <div class="person-name">Dov Strommen</div>
      <div class="person-title">President &amp; CEO</div>
    </div>

    <ul class="contact">
      <li>800-463-5918
        <svg viewBox="0 0 20 20"><path d="M4 3h4l1.5 4-2 1.3a10 10 0 0 0 4.2 4.2l1.3-2 4 1.5v4a1.5 1.5 0 0 1-1.5 1.5A14 14 0 0 1 2.5 4.5 1.5 1.5 0 0 1 4 3z" fill="var(--on-green)"/></svg>
      </li>
      <li>www.petalquarry.example
        <svg viewBox="0 0 20 20"><circle cx="10" cy="10" r="7.5" fill="none" stroke="var(--on-green)" stroke-width="1.6"/><ellipse cx="10" cy="10" rx="3.3" ry="7.5" fill="none" stroke="var(--on-green)" stroke-width="1.4"/><path d="M2.5 10h15M4 6h12M4 14h12" stroke="var(--on-green)" stroke-width="1.2"/></svg>
      </li>
      <li>dovstrommen@petalquarry.example
        <svg viewBox="0 0 20 20"><rect x="2" y="4.5" width="16" height="11" rx="1" fill="none" stroke="var(--on-green)" stroke-width="1.8"/><path d="M2.5 5l7.5 6 7.5-6" fill="none" stroke="var(--on-green)" stroke-width="1.8"/></svg>
      </li>
      <li>31 Harlow Ln, Bexmoor, NJ 07813
        <svg viewBox="0 0 20 20"><path d="M10 18s-6-6.2-6-10.5a6 6 0 0 1 12 0C16 11.8 10 18 10 18z" fill="var(--on-green)"/><circle cx="10" cy="7.5" r="2.2" fill="var(--green-deep)"/></svg>
      </li>
    </ul>
  </div>
</body>
</html>
```